Corvana Tongue Works, LLC

We need a business card that includes information about our business and conveys a reliable business that provides document translation services and interpreters for a variety of corporate and individual clients. We want to come across as professional, reliable, yet approachable. It should include the following on one side:

ESL / ENL Language Classes, Private Lessons, and Online Tutors
PLEXA Training and Testing
Translating & Interpreting Services
Contact us about Over-the-Phone Interpreting in over 200 languages
24/7/365
www.corvanatongue.example

The other side should include (555) 481-3062

Rhoda Pelling, President
482 Garnet Ave., Ste. 219
Indianapolis, IN 40917

Please add USA as part of the address. Also, please add rmpelling@corvanatongueworks.example as the e-mail address. Thank you.

Target Market(s)

Business professionals, their families, the international community

Industry/Entity Type

Business

Contact Information for Business Card

24/7/365
www.corvanatongue.example

(555) 481-3062

Rhoda Pelling, President
482 Garnet Ave., Ste. 219
Indianapolis, IN 40917
USA

Font styles to use
Sans Serif

Colors

Designer to choose colors to be used in the design.

Requirements
Must have
• See project description
• e-mail address and web address
• Phone number
Nice to have
• a globe
• physical address
Should not have
• Should not have the same color scheme as other agencies in our market in Indiana unless it is blue and black. No purple or yellow.

```html
<!DOCTYPE html>
<html lang="en">
<head>
<meta charset="utf-8">
<title>Corvana Tongue Works — Business Card</title>
<link href="https://fonts.googleapis.com/css2?family=Work+Sans:wght@400;500&family=Oswald:wght@600&display=swap" rel="stylesheet">
<style>
  :root {
    --backdrop: #222224;
    --card: #151515;
    --card-edge: #262626;
    --ink-gloss: #b9b9bb;
    --ink-soft: #8f8f92;
    --ink-spot: #3c3c3e;
    --rule: #6e6e70;
  }
  * { box-sizing: border-box; margin: 0; padding: 0; }
  html, body {
    width: 1200px; height: 900px; overflow: hidden;
    background: var(--backdrop);
    font-family: "Work Sans", sans-serif;
  }
  .canvas {
    position: relative; width: 1200px; height: 900px;
    display: flex; flex-direction: column; align-items: center;
    justify-content: center; gap: 24px;
  }
  .card {
    position: relative; width: 700px; height: 400px;
    background: var(--card);
    border: 1px solid var(--card-edge);
    box-shadow: 0 10px 30px rgba(0,0,0,.45);
    overflow: hidden;
  }

  /* Front: brand + services */
  .brand {
    position: absolute; top: 52px; left: 0; right: 0;
    display: flex; align-items: center; justify-content: center; gap: 22px;
  }
  .brand-dot {
    width: 108px; height: 108px; border-radius: 50%;
    border: 3px solid var(--ink-spot);
  }
  .brand-name {
    color: var(--ink-gloss); font-weight: 400;
    font-size: 34px; line-height: 1.05;
  }
  .services {
    position: absolute; top: 196px; left: 60px; right: 60px;
    text-align: center; color: var(--ink-soft);
    font-size: 15px; line-height: 1.4;
  }
  .services .rule {
    height: 1px; background: var(--rule); margin: 2px 0 6px;
  }

  /* Back: name + contact */
  .person {
    position: absolute; left: 40px; top: 150px; text-align: right; width: 225px;
  }
  .person-name {
    font-family: "Oswald", sans-serif; font-weight: 600;
    font-size: 34px; letter-spacing: .5px; color: var(--ink-spot);
    text-transform: uppercase; line-height: 1; white-space: nowrap;
  }
  .person-role { font-size: 16px; color: var(--ink-spot); margin-top: 4px; }
  .divider {
    position: absolute; left: 288px; top: 118px;
    width: 1px; height: 150px; background: var(--rule);
  }
  .contact {
    position: absolute; left: 310px; top: 120px; right: 16px;
    color: var(--ink-gloss); font-size: 15.5px; line-height: 1.35;
    white-space: nowrap;
  }
  .contact .address { margin-bottom: 8px; }
  .contact .line { display: flex; align-items: center; gap: 9px; }
  .contact svg { width: 12px; height: 12px; flex: none; }
</style>
</head>
<body>
<main class="canvas">
  <section class="card card-front">
    <div class="brand">
      <div class="brand-dot"></div>
      <div class="brand-name">Corvana<br>Tongue<br>Works, LLC</div>
    </div>
    <div class="services">
      <p>ESL / ENL Language Classes, Private Lessons, and Online Tutors</p>
      <p>PLEXA Training and Testing</p>
      <p>Translating &amp; Interpreting Services</p>
      <div class="rule"></div>
      <p>Contact us about Over-the-Phone Interpreting in over 200 languages</p>
      <p>24/7/365</p>
    </div>
  </section>

  <section class="card card-back">
    <div class="person">
      <div class="person-name">Rhoda Pelling</div>
      <div class="person-role">President</div>
    </div>
    <div class="divider"></div>
    <div class="contact">
      <p class="address">482 Garnet Ave., Ste. 219<br>Indianapolis, IN 40917 USA</p>
      <p class="line">
        <svg viewBox="0 0 16 16" aria-hidden="true"><path d="M4 1l3 3-2 2c1 2 3 4 5 5l2-2 3 3-2 2C7 14 2 9 2 3z" fill="var(--ink-soft)"/></svg>
        (555) 481-3062</p>
      <p class="line">
        <svg viewBox="0 0 16 16" aria-hidden="true"><rect x="1.5" y="3.5" width="13" height="9" fill="none" stroke="var(--ink-soft)" stroke-width="1.4"/><path d="M1.5 3.5l6.5 5 6.5-5" fill="none" stroke="var(--ink-soft)" stroke-width="1.4"/></svg>
        rmpelling@corvanatongueworks.example</p>
      <p class="line">
        <svg viewBox="0 0 16 16" aria-hidden="true"><circle cx="8" cy="8" r="6.5" fill="none" stroke="var(--ink-soft)" stroke-width="1.3"/><ellipse cx="8" cy="8" rx="2.8" ry="6.5" fill="none" stroke="var(--ink-soft)" stroke-width="1.1"/><path d="M1.5 8h13" stroke="var(--ink-soft)" stroke-width="1.1"/></svg>
        www.corvanatongue.example</p>
    </div>
  </section>
</main>
</body>
</html>
```